Sophisticated, clean website reflecting my feminine, playful side to sell my abstract art,

I need a website no more than 3 pages to showcase my paintings, a little about me and some contact info. I do abstracts so looking for something a little edgy, yet feminine and current.
Updates

Hi there, These are some artists websites that I Iike: Marnelvoss.com (I like how airy it is) peterwallombry.com garethpolvens.com (I like how it scrolls) I'll need a place for a photo ( a headshot-i do not have it yet so I'll need to be able to upload that later) as well as an area for my bio. Also, it's important that I will be able to upload any new photos and descriptions easily so it should be user friendly. Lastly, I like in a sunny place so would like to have this seem upbeat and playful as that is how i like to paint. thanks-I'm trying to upload my photos now -

Target Market(s)

ppl ages 35-70 who want large scale art for their homes

Industry/Entity Type

art

Coding

Coded - Design and coding required

Number of Pages Required

3 page

Colors

Designer to choose colors to be used in the design.

Requirements
Must have
• photos of my art, a place for my bio, be easy to reach me. tasteful-nothing too "in your face" -my clients are pretty high end and organized. They like clean lines
Nice to have
• sophisticated background, muted tones in the back-similar clean font throughout-no cursive
Should not have
• too many dark areas. Too many blocks of color. Too serious.

```html
<!DOCTYPE html>
<html lang="en">
<head>
<meta charset="utf-8">
<title>Helena Marwick Art</title>
<link rel="stylesheet" href="https://fonts.googleapis.com/css2?family=Noto+Serif:wght@300;400;500&display=swap">
<style>
:root{
  --ink:#2b2b2b;
  --text:#3a3a3a;
  --accent:#f2703f;
  --header-bg:#f4f4f4;
  --blush:#fdf2f2;
  --white:#ffffff;
  --muted:#555555;
}
*{box-sizing:border-box;margin:0;padding:0}
html,body{width:1200px;height:3415px;overflow:hidden;background:var(--white)}
body{position:relative;font-family:"Noto Serif",Georgia,serif;color:var(--text)}
.abs{position:absolute}
.site-header{left:0;top:0;width:1200px;height:97px;background:var(--header-bg)}
.brand{left:75px;top:22px;font-size:44px;font-weight:400;color:var(--ink);letter-spacing:1px}
.menu-toggle{left:1097px;top:34px}
h1,h2{font-weight:300;color:var(--ink);letter-spacing:1px}
.hero-title{left:75px;top:240px;font-size:57px;line-height:61px}
.hero-title span{color:var(--accent)}
.lead{font-size:17px;line-height:29px;letter-spacing:.3px}
.hero-text{left:75px;top:435px;width:490px}
.btn{display:flex;align-items:center;justify-content:center;border:1px solid var(--accent);color:var(--accent);font-size:16px;font-weight:500;letter-spacing:.5px;background:transparent}
.hero-btn{left:75px;top:549px;width:182px;height:54px}
.hero-frame{left:587px;top:155px;width:540px;height:473px;background:#efefef;box-shadow:0 4px 16px rgba(0,0,0,.08)}
.hero-art{left:601px;top:170px;width:512px;height:527px;background:linear-gradient(140deg,#4fae7a 0%,#d9d6cf 30%,#1f4a3e 55%,#9c9a8e 75%,#c9b77a 100%);box-shadow:0 6px 18px rgba(0,0,0,.15)}
.blush-band{left:0;top:783px;width:1200px;height:1205px}
.card{background:var(--white);box-shadow:0 6px 30px rgba(0,0,0,.06)}
.about-card{left:0;top:783px;width:884px;height:592px}
.section-title{font-size:49px}
.about-title{left:75px;top:888px}
.body-copy{font-size:17px;line-height:35px;letter-spacing:.2px}
.about-copy{left:75px;top:962px;width:600px}
.about-btn{left:75px;top:1203px;width:182px;height:54px}
.about-photo{left:704px;top:840px;width:436px;height:478px;background:linear-gradient(120deg,#e9e3da 0%,#d8cbbb 45%,#7e8fa4 75%,#5d6e82 100%)}
.gallery-title{left:75px;top:1432px}
.painting{width:242px;height:326px;box-shadow:0 6px 14px rgba(0,0,0,.15)}
.p1{left:75px;top:1539px;background:linear-gradient(150deg,#d8d2cf,#6b4a7c 50%,#bfb6c1)}
.p2{left:345px;top:1585px;background:linear-gradient(150deg,#c99a2a,#d2a84a 45%,#8a3a1f 70%,#e9dcc5)}
.p3{left:615px;top:1539px;background:linear-gradient(90deg,#8e97a8 0%,#d9cdb9 28%,#0e8f85 42%,#0a6f66 100%)}
.p4{left:885px;top:1585px;background:linear-gradient(150deg,#ecebe4,#7d98cf 40%,#e3d26a 60%,#e6e3dc)}
.abstract-card{left:331px;top:2056px;width:869px;height:592px}
.abstract-art{left:75px;top:2113px;width:436px;height:478px;background:linear-gradient(170deg,#25a6b4 0%,#56b6ae 28%,#e8b20b 55%,#d99c10 80%,#8fa39a 100%)}
.abstract-title{left:535px;top:2162px}
.abstract-copy{left:535px;top:2234px;width:600px}
.abstract-btn{left:535px;top:2475px;width:201px;height:54px}
.contact-band{left:0;top:2727px;width:1200px;height:432px;background:linear-gradient(110deg,#efe3f2 0%,#d8c2e3 30%,#e6b6d8 55%,#c8a6da 78%,#eadff0 100%)}
.contact-box{left:75px;top:2803px;width:513px;height:282px;background:rgba(255,255,255,.72);text-align:center}
.contact-title{position:absolute;left:0;width:100%;top:22px;font-size:47px;line-height:60px}
.contact-line{position:absolute;left:0;width:100%;font-size:23px;line-height:30px;letter-spacing:1px;color:var(--ink)}
.contact-btn{left:156px;top:192px;width:200px;height:53px}
.footer-brand{left:0;width:1200px;top:3212px;text-align:center;font-size:42px;font-weight:300;color:var(--ink);letter-spacing:1px}
.copyright{left:0;width:1200px;top:3284px;text-align:center;font-size:17px;letter-spacing:.5px}
.social{left:480px;top:3322px;width:240px;display:flex;justify-content:space-between}
.social span{width:24px;height:24px;border-radius:50%;background:var(--ink)}
</style>
</head>
<body>
<header class="abs site-header">
  <div class="abs brand">Helena Marwick Art</div>
  <svg class="abs menu-toggle" width="30" height="28" viewBox="0 0 30 28" aria-label="Menu">
    <rect x="6" y="0" width="24" height="4" fill="#2b2b2b"/><rect x="0" y="8" width="30" height="4" fill="#2b2b2b"/>
    <rect x="6" y="16" width="24" height="4" fill="#2b2b2b"/><rect x="0" y="24" width="30" height="4" fill="#2b2b2b"/>
  </svg>
</header>

<section>
  <h1 class="abs hero-title">Welcome to<br>Helena Marwick<br><span>Art</span></h1>
  <p class="abs lead hero-text">Sed ut perspiciatis unde omnis iste natus error sit voluptatem accusantium doloremque laudantium, totam rem aperiam, eaque ipsa quae.</p>
  <a class="abs btn hero-btn">View My Painting</a>
  <svg class="abs" style="left:75px;top:674px" width="90" height="18" viewBox="0 0 90 18" aria-label="Slide controls">
    <path d="M30 9H4M11 2 3 9l8 7" stroke="#555" stroke-width="4" fill="none"/>
    <path d="M58 9h26M77 2l8 7-8 7" stroke="#f2703f" stroke-width="4" fill="none"/>
  </svg>
  <div class="abs hero-frame"></div>
  <div class="abs hero-art" role="img" aria-label="Abstract painting in green, teal and black brushstrokes"></div>
</section>

<svg class="abs blush-band" width="1200" height="1205" viewBox="0 0 1200 1205"><polygon points="1140,0 1200,0 1200,1205 0,1205" fill="#fdf2f2"/></svg>

<section>
  <div class="abs card about-card"></div>
  <h2 class="abs section-title about-title">About Me</h2>
  <p class="abs body-copy about-copy">Sed ut perspiciatis unde omnis iste natus error sit voluptatem accusantium doloremque laudantium, totam rem aperiam, eaque ipsa quae ab illo inventore veritatis et quasi architecto beatae vitae dicta sunt explicabo. Nemo enim ipsam voluptatem quia voluptas sit aspernatur aut odit aut fugit, sed quia consequuntur magni dolores eos qui ratione voluptatem sequi nesciunt.</p>
  <a class="abs btn about-btn">More About Me</a>
  <div class="abs about-photo" role="img" aria-label="Photo of the artist seated beside her canvas holding paintbrushes"></div>
</section>

<section>
  <h2 class="abs section-title gallery-title">My Painting Gallery</h2>
  <svg class="abs" style="left:1038px;top:1457px" width="90" height="18" viewBox="0 0 90 18" aria-label="Gallery controls">
    <path d="M30 9H4M11 2 3 9l8 7" stroke="#555" stroke-width="4" fill="none"/>
    <path d="M58 9h26M77 2l8 7-8 7" stroke="#f2703f" stroke-width="4" fill="none"/>
  </svg>
  <div class="abs painting p1" role="img" aria-label="Abstract painting with purple floral bursts"></div>
  <div class="abs painting p2" role="img" aria-label="Abstract painting in ochre, rust and navy swirls"></div>
  <div class="abs painting p3" role="img" aria-label="Abstract painting with a teal field and pale stripe"></div>
  <div class="abs painting p4" role="img" aria-label="Abstract painting with blue and yellow strokes on white"></div>
</section>

<section>
  <div class="abs card abstract-card"></div>
  <div class="abs abstract-art" role="img" aria-label="Textured abstract painting in turquoise and golden yellow"></div>
  <h2 class="abs section-title abstract-title">Abstracts</h2>
  <p class="abs body-copy abstract-copy">Sed ut perspiciatis unde omnis iste natus error sit voluptatem accusantium doloremque laudantium, totam rem aperiam, eaque ipsa quae ab illo inventore veritatis et quasi architecto beatae vitae dicta sunt explicabo. Nemo enim ipsam voluptatem quia voluptas sit aspernatur aut odit aut fugit, sed quia consequuntur magni dolores eos qui ratione voluptatem sequi nesciunt.</p>
  <a class="abs btn abstract-btn">View Our Paintings</a>
</section>

<section>
  <div class="abs contact-band" role="img" aria-label="Soft watercolour wash in lavender and pink"></div>
  <div class="abs contact-box">
    <h2 class="contact-title">Contact Info</h2>
    <div class="contact-line" style="top:96px">1-880-555-0142</div>
    <div class="contact-line" style="top:133px">hello@helenamarwick.art</div>
    <a class="abs btn contact-btn">Contact Us</a>
  </div>
</section>

<footer>
  <div class="abs footer-brand">Helena Marwick Art</div>
  <p class="abs copyright">Copyright © 2022 Lumen Folio · All Rights Reserved.</p>
  <div class="abs social" aria-label="Social links"><span></span><span></span><span></span><span></span><span></span></div>
</footer>
</body>
</html>
```